Industry automation wholesale website

www.velturo.eu provides solutions for automation, building automation and digital signage.

Our products are rugged, reliable, energy saving and representative.

Scope of pages:
● welcome page
- scope of products
- applications, success stories and news
● category page
- short introduction
- sub categories
- product highlights
● product page
- short introduction
- about 3 to 4 pictures
- technical specifications: materials, dimensions
- price
- related products

Optional:
● contact page
- address
- contact form
● blog
- picture
- text
● logo
● favicon / apple touch icon

Conclusion:
● We need a professionally looking site
● Bright colors (e.g. white, grey, metalic colors, blue)

some pages we like:
http://www.prandek.de/
http://www.morvalix.de/

Target Market(s)

Our target market is the industrial sector
● Target audience: engineering and IT professionals

Industry/Entity Type

Building

Requirements
Must have
• ● only use free available fonts e.g. Lumara Type Library (http://www.lumaratype.com/webfonts)
Should not have
• ● sound
● flash

```html
<!DOCTYPE html>
<html lang="en">
<head>
<meta charset="utf-8">
<title>Velturo – Industrial Automation</title>
<link href="https://fonts.googleapis.com/css2?family=Arimo:wght@400;700&display=swap" rel="stylesheet">
<style>
:root{
  --brand:#1b6690;
  --heading:#1d5177;
  --nav-top:#1c6d9c;
  --nav-bottom:#0e3d5b;
  --text:#333;
  --muted:#8a8a8a;
  --hero-band:#def2fb;
  --hero-panel:#fff6f6;
  --line:#c9c9c9;
  --footer:#4a4a4a;
  --dot:#888;
}
*{box-sizing:border-box;margin:0;padding:0}
html,body{width:1048px;height:1200px;overflow:hidden;background:#fff}
body{font-family:"Arimo",Arial,sans-serif;color:var(--text);position:relative}
.abs{position:absolute}
ul{list-style:none}

/* header */
.brand{left:126px;top:18px}
.brand-name{font-size:38px;color:var(--brand);font-weight:400;letter-spacing:1px;line-height:1}
.brand-tag{font-size:10px;color:var(--brand);margin-top:3px}
.call{right:125px;top:36px;display:flex;align-items:center;gap:6px;font-size:18px;color:#333}
.call small{font-size:13px;color:#666}

/* nav */
.nav{left:123px;top:87px;width:802px;height:46px;background:linear-gradient(var(--nav-top),var(--nav-bottom));display:flex;align-items:center}
.nav a{color:#fff;text-decoration:none;font-size:12.5px}
.nav ul{display:flex;margin-left:39px;gap:0}
.nav li{margin-right:44px}
.nav-search{position:absolute;right:11px;top:11px;width:181px;height:24px;background:#fff;border-radius:4px;font-size:10px;color:#888;padding:5px 10px}
.nav-search svg{position:absolute;right:8px;top:5px}

/* hero */
.hero-band{left:0;top:134px;width:1048px;height:260px;background:var(--hero-band)}
.hero{left:123px;top:134px;width:802px;height:244px;background:var(--hero-panel)}
.hero-photo{left:37px;top:19px;width:275px;height:205px;background:linear-gradient(135deg,#f2f2f2,#c9cdd2 60%,#e6e8ea)}
.hero-title{left:382px;top:58px;font-size:22px;font-weight:700;color:var(--heading)}
.hero-specs{left:384px;top:101px;font-size:14px;color:#666;line-height:22.5px}
.hero-specs b{font-weight:400;color:var(--brand)}
.dots{left:720px;top:218px;display:flex;gap:4px}
.dots span{width:12px;height:12px;border-radius:50%;background:var(--dot)}
.dots span:first-child{background:var(--heading)}

/* welcome */
.welcome{left:123px;top:412px;width:802px;text-align:center}
.welcome h1{font-size:19px;font-weight:400;color:var(--heading)}
.welcome p{font-size:10.5px;color:var(--muted);line-height:20.5px;margin-top:9px}

.section-title{font-size:19px;font-weight:400;color:var(--heading)}

/* products */
.product{width:158px}
.product-photo{width:158px;height:129px;border:1px solid var(--line);display:flex;align-items:center;justify-content:center}
.product-photo div{width:90px;height:90px}
.product h3{font-size:12.5px;font-weight:400;color:var(--brand);line-height:20.5px;margin-top:8px;padding-left:1px}
.product p{font-size:10px;color:var(--muted);line-height:20.5px;margin-top:4px}

/* login */
.login{left:669px;top:549px;width:254px;height:260px;border:1px solid var(--line)}
.login-mail{left:66px;top:30px;font-size:19px;color:var(--brand)}
.field{left:20px;width:211px;height:32px;border:1px solid #c4c4c4;border-radius:6px;font-size:10px;color:#333;padding:10px 12px}
.submit{left:137px;top:189px;width:94px;height:31px;border-radius:4px;background:linear-gradient(var(--nav-top),var(--nav-bottom));color:#fff;font-size:12.5px;display:flex;align-items:center;justify-content:center}

/* lists */
.link-list li{font-size:11px;color:#333;height:24.6px;display:flex;align-items:center;gap:9px}
.testimonial{left:670px;top:836px;width:255px}
.testimonial p{font-size:11px;color:var(--muted);line-height:20.5px;margin:14px 0 0 20px}
.quote{font-size:28px;color:#999;font-family:Georgia,serif;line-height:1}
.author{text-align:right;font-size:11px;color:var(--heading);line-height:16.5px}

/* footer */
.footer{left:0;top:1120px;width:1048px;height:80px;background:var(--footer);color:#fff}
.footer-links{left:124px;top:21px;font-size:11px;display:flex}
.footer-links span{margin:0 11px}
.copyright{left:124px;top:46px;font-size:11px}
.social{top:28px;width:26px;height:26px;border-radius:50%;box-shadow:0 1px 3px rgba(0,0,0,.5)}
</style>
</head>
<body>

<header>
  <div class="abs brand">
    <div class="brand-name">velturo</div>
    <div class="brand-tag">analog digital measurements</div>
  </div>
  <div class="abs call">
    <svg width="18" height="30" viewBox="0 0 18 30" aria-hidden="true"><path d="M6 2c-3 1-5 4-4 9 1 6 4 12 8 15 2 2 4 2 6 1l-3-6c-1 0-2 1-3 0-2-3-3-6-3-9 0-1 1-1 2-1L8 2z" fill="#333"/></svg>
    <span>Call <small>- 49 211 555 01 23</small></span>
  </div>
</header>

<nav class="abs nav">
  <ul>
    <li><a href="#">Home</a></li>
    <li><a href="#">About us</a></li>
    <li><a href="#">products</a></li>
    <li><a href="#">Search</a></li>
    <li><a href="#">Shopping cart</a></li>
    <li><a href="#">Contact us</a></li>
  </ul>
  <div class="nav-search">Search
    <svg width="14" height="12" viewBox="0 0 14 12" aria-hidden="true"><circle cx="5" cy="5" r="3.5" fill="none" stroke="#999" stroke-width="1.5"/><path d="M7.5 7.5l5 4" stroke="#999" stroke-width="2"/></svg>
  </div>
</nav>

<div class="abs hero-band"></div>
<section class="abs hero">
  <div class="abs hero-photo" role="img" aria-label="Photo of hands typing on a touch panel PC screen"></div>
  <h2 class="abs hero-title">Touch Panel PC / Bedienterminal</h2>
  <div class="abs hero-specs">
    <div><b>industrial</b> : IP65,24/7 Continuius operation</div>
    <div><b>performance</b> : Corvex Dual Core C525 1,8 GHz</div>
    <div><b>fanless</b> : low heat emission, power saving</div>
  </div>
  <div class="abs dots"><span></span><span></span><span></span><span></span></div>
</section>

<section class="abs welcome">
  <h1>Welcome to Velturo</h1>
  <p>Velturo is your specialist partner for industrial automation. We at Velturo provide individual solutions for unitized measurement and offer the whole range of products,<br>from interface converter over RS-485 and ModBus-Modules and to Embedded Systems and powerful Panel-PCs</p>
</section>

<h2 class="abs section-title" style="left:123px;top:505px">Our products</h2>

<article class="abs product" style="left:122px;top:543px">
  <div class="product-photo"><div role="img" aria-label="Photo of a blue RS485 remote IO module" style="background:linear-gradient(135deg,#6d8fd8,#3f5fa8);border-radius:8px"></div></div>
  <h3>Modbus RTU / RS485<br>Remote Io Modules</h3>
  <p>RS485 Remote IO modules are ideal to realize decentralized distributed IO units over long distances.</p>
</article>
<article class="abs product" style="left:296px;top:543px">
  <div class="product-photo"><div role="img" aria-label="Photo of an industrial touch panel computer" style="width:84px;height:76px;background:linear-gradient(135deg,#2c2c2c,#555);border:8px solid #222"></div></div>
  <h3>Touch Panel Industry<br>Computer</h3>
  <p>RS485 Remote IO modules are ideal to realize decentralized distributed IO units over long distances.</p>
</article>
<article class="abs product" style="left:469px;top:543px">
  <div class="product-photo"><div role="img" aria-label="Photo of a fanless embedded box PC" style="width:118px;height:58px;background:linear-gradient(#9a9a9a,#333);border-radius:3px"></div></div>
  <h3>Embedded System For<br>Industrial automation</h3>
  <p>RS485 Remote IO modules are ideal to realize decentralized distributed IO units over long distances.</p>
</article>

<aside class="abs login">
  <svg class="abs" style="left:7px;top:18px" width="42" height="36" viewBox="0 0 42 36" aria-hidden="true">
    <path d="M2 14L21 2l19 12v20H2z" fill="#1e8fd6"/><path d="M2 14l19 12 19-12v20H2z" fill="#3aaef0"/>
    <circle cx="21" cy="13" r="6" fill="none" stroke="#fff" stroke-width="2"/></svg>
  <div class="abs login-mail">info@velturo.de</div>
  <div class="abs field" style="top:86px">User Name :</div>
  <div class="abs field" style="top:139px">Pass word :</div>
  <div class="abs submit">Submit</div>
</aside>

<section>
  <h2 class="abs section-title" style="left:123px;top:836px">Range of products</h2>
  <ul class="abs link-list" style="left:131px;top:873px">
    <li><svg width="11" height="8" viewBox="0 0 11 8"><path d="M0 4h9M6 1l3 3-3 3" stroke="#666" fill="none" stroke-width="1.2"/></svg>RS422 / RS485 Converter</li>
    <li><svg width="11" height="8" viewBox="0 0 11 8"><path d="M0 4h9M6 1l3 3-3 3" stroke="#666" fill="none" stroke-width="1.2"/></svg>RS422 / RS485 Repeater</li>
    <li><svg width="11" height="8" viewBox="0 0 11 8"><path d="M0 4h9M6 1l3 3-3 3" stroke="#666" fill="none" stroke-width="1.2"/></svg>RS485 Remote Io</li>
    <li><svg width="11" height="8" viewBox="0 0 11 8"><path d="M0 4h9M6 1l3 3-3 3" stroke="#666" fill="none" stroke-width="1.2"/></svg>RS485 Modbus Io</li>
    <li><svg width="11" height="8" viewBox="0 0 11 8"><path d="M0 4h9M6 1l3 3-3 3" stroke="#666" fill="none" stroke-width="1.2"/></svg>Embedded System</li>
    <li><svg width="11" height="8" viewBox="0 0 11 8"><path d="M0 4h9M6 1l3 3-3 3" stroke="#666" fill="none" stroke-width="1.2"/></svg>PCI-Series</li>
    <li><svg width="11" height="8" viewBox="0 0 11 8"><path d="M0 4h9M6 1l3 3-3 3" stroke="#666" fill="none" stroke-width="1.2"/></svg>Industry PC</li>
    <li><svg width="11" height="8" viewBox="0 0 11 8"><path d="M0 4h9M6 1l3 3-3 3" stroke="#666" fill="none" stroke-width="1.2"/></svg>Industrial Display</li>
    <li><svg width="11" height="8" viewBox="0 0 11 8"><path d="M0 4h9M6 1l3 3-3 3" stroke="#666" fill="none" stroke-width="1.2"/></svg>Din Rail Power Supply</li>
  </ul>

  <h2 class="abs section-title" style="left:369px;top:836px">Language</h2>
  <ul class="abs link-list" style="left:367px;top:873px">
    <li><svg width="11" height="8" viewBox="0 0 11 8"><path d="M0 4h9M6 1l3 3-3 3" stroke="#666" fill="none" stroke-width="1.2"/></svg>English</li>
    <li><svg width="11" height="8" viewBox="0 0 11 8"><path d="M0 4h9M6 1l3 3-3 3" stroke="#666" fill="none" stroke-width="1.2"/></svg>Deutsch</li>
    <li><svg width="11" height="8" viewBox="0 0 11 8"><path d="M0 4h9M6 1l3 3-3 3" stroke="#666" fill="none" stroke-width="1.2"/></svg>Espanol</li>
    <li><svg width="11" height="8" viewBox="0 0 11 8"><path d="M0 4h9M6 1l3 3-3 3" stroke="#666" fill="none" stroke-width="1.2"/></svg>Francais</li>
    <li><svg width="11" height="8" viewBox="0 0 11 8"><path d="M0 4h9M6 1l3 3-3 3" stroke="#666" fill="none" stroke-width="1.2"/></svg>Italiano</li>
    <li><svg width="11" height="8" viewBox="0 0 11 8"><path d="M0 4h9M6 1l3 3-3 3" stroke="#666" fill="none" stroke-width="1.2"/></svg>Nederlands</li>
    <li><svg width="11" height="8" viewBox="0 0 11 8"><path d="M0 4h9M6 1l3 3-3 3" stroke="#666" fill="none" stroke-width="1.2"/></svg>Chinese</li>
  </ul>

  <h2 class="abs section-title" style="left:526px;top:836px">Editorial</h2>
  <ul class="abs link-list" style="left:526px;top:874px">
    <li><svg width="11" height="8" viewBox="0 0 11 8"><path d="M0 4h9M6 1l3 3-3 3" stroke="#666" fill="none" stroke-width="1.2"/></svg>Terms and Conditions</li>
    <li><svg width="11" height="8" viewBox="0 0 11 8"><path d="M0 4h9M6 1l3 3-3 3" stroke="#666" fill="none" stroke-width="1.2"/></svg>Masthesd</li>
  </ul>

  <div class="abs testimonial">
    <h2 class="section-title">Testimonals</h2>
    <span class="abs quote" style="left:-5px;top:24px">&#8220;</span>
    <p>Velturo is your specialist partner for indus-trial automation. We at Velturo provide individual solutions for unitized measure-ment and offer the whole range of products, from interface converter &nbsp;to Embedded Systems and powerful Panel-PCs.</p>
    <div class="quote" style="text-align:right;margin:-6px 10px 0 0">&#8221;</div>
    <div class="author">Lena Hartwig<br>Posed on 20 Dec 2014</div>
  </div>
</section>

<footer class="abs footer">
  <div class="abs footer-links">Home<span>|</span>About us<span>|</span>products<span>|</span>Search<span>|</span>Shopping cart<span>|</span>Contact us</div>
  <div class="abs copyright">Copyright 2014 Velturo.All Right Reseved.</div>
  <div class="abs social" style="left:865px;background:radial-gradient(circle at 40% 35%,#5b86d6,#2a4f9a)"></div>
  <div class="abs social" style="left:897px;background:radial-gradient(circle at 40% 35%,#8fdcff,#2fa6e0)"></div>
</footer>

</body>
</html>
```